Design letter head and business card

Hello,

you should design a business card and letter paper for Kranichflug Marketing. In German we write this word with K insteat of C.

Company does not have a logo. But in general, we write Kranichflug Marketing in 2 lines.
First line red: KRANICHFLUG
Second line gray: MARKETING

Red (or wine red) and Gray / Black are our favorite colors.

Company slogan: "Fresh Ground Online Marketing".

Company offers SEO, SEM, SEA, AdWords, Conversion Optimization, Online Markting Consulting ...

The website is old, please do not use this as base for your task.

German letter paper sizes:
Viawable Dimensions : 210 x 297 mm
Needed file dimensions: 212 x 299 mm

Informations to include:

Address:
Kranichflug Marketing GmbH
Lindenweg 23
71592 Rebenfeld
Germany

Geschäftsführer | CEO: Bernhard Olzner

Phone: +49 (0) 6234 846 27 05

Fax: +49 (0) 6234 846 27 88

Mail: info@kranichflug-beispiel.de

Web: www.kranichflug-beispiel.de

Amtsgericht Suttgart, HRB 537264

Bank: Rosenauer Bank
IBAN: DE827315480900XXXXXXXX
BIC: GENODES1RSQ

Thanks

Bernhard

Target Market(s)

People who likes to win the online marketing game.

Industry/Entity Type

Business

Contact Information for Business Card

Here is the personal text on the card:

Name:
Bernhard Olzner

Title:
Geschäftsführer | CEO

Address:
Kranichflug Marketing GmbH
Lindenweg 23
71592 Rebenfeld
Germany

Phone:
+49 (0) 6234 846 27 05

Fax:
+49 (0) 6234 846 27 88

Mail:
olzner@kranichflug-beispiel.de

Web:
www.kranichflug-beispiel.de

Business Card:
Viewable Dimensions: 85 x 55 mm
Needed file dimensions: 87 x 57mm

Font styles to use
Sans Serif

Requirements
Nice to have
• It would be great to see the dynamics of a helicopter.

```html
<!DOCTYPE html>
<html lang="de">
<head>
<meta charset="utf-8">
<title>Kranichflug Marketing – Visitenkarte</title>
<link rel="stylesheet" href="https://fonts.googleapis.com/css2?family=Saira+Semi+Condensed:wght@400;600;700&display=swap">
<style>
  :root {
    --page: #ffffff;
    --card: #e7e7e9;
    --tab: #a5a6a9;
    --wine: #8b1e22;
    --ink: #2a2a2c;
    --ink-soft: #3a3a3c;
    --paper-text: #f4eeee;
  }
  * { margin: 0; padding: 0; box-sizing: border-box; }
  html, body {
    width: 1200px; height: 1000px; overflow: hidden;
    background: var(--page);
    font-family: "Saira Semi Condensed", "Arial Narrow", sans-serif;
    color: var(--ink);
  }
  .canvas { position: relative; width: 1200px; height: 1000px; }

  .card {
    position: absolute;
    width: 700px; height: 459px;
    background: var(--card);
    box-shadow: 0 2px 8px rgba(0,0,0,0.18);
    overflow: hidden;
  }
  .card--front { left: 460px; top: 30px; }
  .card--back  { left: 40px;  top: 511px; }

  .card__tab { position: absolute; top: 0; left: 240px; background: var(--tab); }
  .card--front .card__tab { width: 212px; height: 38px; }
  .card--back  .card__tab { width: 215px; height: 44px; }

  .wordmark { position: absolute; text-align: center; line-height: 0.95; white-space: nowrap; }
  .wordmark__name { display: block; font-weight: 700; color: var(--ink); letter-spacing: 0.5px; }
  .wordmark__tagline { display: block; font-weight: 400; color: var(--ink-soft); }

  .card--front .wordmark { left: 130px; top: 210px; width: 440px; }
  .card--front .wordmark__name { font-size: 52px; }
  .card--front .wordmark__tagline { font-size: 22px; margin-top: 12px; }

  .card--back .wordmark { left: 20px; top: 70px; width: 170px; }
  .card--back .wordmark__name { font-size: 20px; }
  .card--back .wordmark__tagline { font-size: 8.5px; margin-top: 5px; }

  .band {
    position: absolute; bottom: 0;
    background: var(--wine);
    color: var(--paper-text);
    font-weight: 600;
    font-size: 16px;
    text-align: center;
    white-space: nowrap;
    width: 250px; height: 92px;
  }
  .card--front .band { left: 212px; padding-top: 18px; }
  .card--back  .band { left: 245px; padding-top: 14px; }

  .contact { position: absolute; left: 160px; width: 380px; text-align: center; white-space: nowrap; }
  .contact__name { font-size: 27px; font-weight: 700; color: var(--wine); line-height: 1.1; }
  .contact__role { font-size: 20px; color: var(--ink); margin-top: 4px; }
  .contact--person { top: 56px; }
  .contact--address { top: 175px; font-size: 17px; line-height: 1.35; font-style: normal; }
  .contact--lines { top: 282px; font-size: 17px; line-height: 1.35; }
</style>
</head>
<body>
<main class="canvas">

  <section class="card card--front" aria-label="Visitenkarte Vorderseite">
    <div class="card__tab"></div>
    <div class="wordmark">
      <span class="wordmark__name">KRANICHFLUG<br>MARKETING</span>
      <span class="wordmark__tagline">Fresh Ground Online Marketing</span>
    </div>
    <div class="band">www.kranichflug-beispiel.de</div>
  </section>

  <section class="card card--back" aria-label="Visitenkarte Rückseite">
    <div class="card__tab"></div>
    <div class="wordmark">
      <span class="wordmark__name">KRANICHFLUG<br>MARKETING</span>
      <span class="wordmark__tagline">Fresh Ground Online Marketing</span>
    </div>

    <div class="contact contact--person">
      <p class="contact__name">Bernhard Olzner</p>
      <p class="contact__role">Geschäftsführer | CEO</p>
    </div>

    <address class="contact contact--address">
      Kranichflug Marketing GmbH,<br>
      Lindenweg 23,<br>
      71592 Rebenfeld, Germany
    </address>

    <div class="contact contact--lines">
      <p>Phone: +49 (0) 6234 846 27 05</p>
      <p>Fax: +49 (0) 6234 846 27 88</p>
    </div>

    <div class="band">info@kranichflug-beispiel.de</div>
  </section>

</main>
</body>
</html>
```